Global investment holding company - Business Card Design

Velto Range is a recently incorporated investment holding company. Based in Singapore, it has operations in global emerging markets in the transport & logistics, energy and livestock industries.

Its tagline "Building Growth Together" reflects the company's philosophy of helping countries progress through partnerships which generate employment and share benefits with its society.

We are looking for a business card that reflects our global presence - incorporating the logo design into the business card design. It must have a sophisticated, modern & corporate feel.

Target Market(s)

Investors and high level governmental officials

Industry/Entity Type

Investment

Requirements
Must have
• - Use of shades of blue in logo

-Profile picture

- Name: Dennis Orbeck
- Title: Chairman
- Email: dennis@veltorange-mail.com
- Mob: +65 9154 0826
- Tel: +65 6418 5092
- DID: + 65 6418 5093
- Address: 47 Harrow Lane, #08-03, Singapore 071286

- website: www.veltorange-mail.com

```html
<!DOCTYPE html>
<html lang="en">
<head>
<meta charset="utf-8">
<title>Velto Range – Business Card</title>
<link rel="stylesheet" href="https://fonts.googleapis.com/css2?family=Didact+Gothic&family=PT+Sans:wght@400;700&display=swap">
<style>
  :root {
    --backdrop: #d9dee3;
    --blue-deep: #0a6fc2;
    --blue-mid: #1489d6;
    --blue-light: #27a9e3;
    --band-dark: #0b5fae;
    --band-light: #3d9be0;
    --paper: #ffffff;
    --ink: #3b3b3b;
    --ink-soft: #555a5f;
    --link: #2856a3;
    --photo-warm: #d8c3a2;
    --photo-suit: #2a3446;
  }
  * { box-sizing: border-box; margin: 0; padding: 0; }
  html, body {
    width: 1200px; height: 960px; overflow: hidden;
    background: var(--backdrop);
  }
  .sheet {
    position: relative; width: 1200px; height: 960px;
    display: flex; flex-direction: column; align-items: center; justify-content: center; gap: 40px;
  }
  .card {
    width: 700px; height: 400px; position: relative; overflow: hidden;
    box-shadow: 0 6px 18px rgba(30, 45, 60, 0.18);
  }

  /* Front */
  .card-front {
    background: linear-gradient(200deg, var(--blue-light) 0%, var(--blue-mid) 45%, var(--blue-deep) 100%);
    color: var(--paper);
    display: flex; flex-direction: column; align-items: center; justify-content: center;
  }
  .brand {
    display: flex; align-items: center; gap: 22px;
  }
  .brand-dot {
    width: 110px; height: 110px; border-radius: 50%; background: var(--paper);
  }
  .brand-name {
    font-family: "PT Sans", sans-serif; font-weight: 700;
    font-size: 58px; line-height: 0.95; letter-spacing: 1px; text-transform: uppercase;
    color: var(--paper);
  }
  .tagline {
    margin-top: 34px;
    font-family: "PT Sans", sans-serif; font-weight: 400;
    font-size: 26px; letter-spacing: 1.5px; text-transform: uppercase;
  }

  /* Back */
  .card-back { background: var(--paper); }
  .profile-photo {
    position: absolute; left: 34px; top: 28px; width: 290px; height: 300px;
    background: linear-gradient(180deg, var(--photo-warm) 0%, var(--photo-warm) 55%, var(--photo-suit) 100%);
  }
  .details {
    position: absolute; left: 370px; top: 38px; width: 310px;
    font-family: "Didact Gothic", sans-serif; color: var(--ink);
  }
  .person-name { font-size: 27px; line-height: 1.1; font-weight: 400; }
  .person-title { font-size: 19px; color: var(--ink-soft); margin-top: 2px; }
  .contact-list {
    margin-top: 28px; display: grid; grid-template-columns: 64px 1fr;
    font-size: 16px; line-height: 1.3;
  }
  .contact-list dt, .contact-list dd { white-space: nowrap; }
  .contact-list dd::before { content: ": "; }
  .address { margin-top: 10px; font-size: 16px; line-height: 1.3; }
  .website { margin-top: 22px; font-size: 18px; color: var(--link); }
  .band {
    position: absolute; left: 0; right: 0; bottom: 0; height: 26px;
    background: linear-gradient(180deg, var(--band-dark) 0%, var(--band-dark) 55%, var(--band-light) 100%);
  }
</style>
</head>
<body>
<main class="sheet">
  <section class="card card-front" aria-label="Business card front">
    <div class="brand">
      <span class="brand-dot" aria-hidden="true"></span>
      <span class="brand-name">Velto<br>Range</span>
    </div>
    <p class="tagline">Building Growth Together</p>
  </section>

  <section class="card card-back" aria-label="Business card back">
    <div class="profile-photo" role="img" aria-label="Portrait photo of Dennis Orbeck in a dark suit"></div>
    <div class="details">
      <h1 class="person-name">Dennis Orbeck</h1>
      <p class="person-title">Chairman</p>
      <dl class="contact-list">
        <dt>Email</dt><dd>dennis@veltorange-mail.com</dd>
        <dt>Mob</dt><dd>+65 9154 0826</dd>
        <dt>Tel</dt><dd>+65 6418 5092</dd>
        <dt>DID</dt><dd>+ 65 6418 5093</dd>
      </dl>
      <p class="address">47 Harrow Lane, #08-03,<br>Singapore 071286</p>
      <p class="website">www.veltorange-mail.com</p>
    </div>
    <div class="band" aria-hidden="true"></div>
  </section>
</main>
</body>
</html>
```